Nutrition business needs logo & business card design

We need a business card & logo design for a new company based in Toronto, Ontario Canada called Verdel Wellworks.

We provide nutrition service using metrics as guide to manage client's progress. Our service creates individualized nutrition and lifestyle strategies that focuses on improving Performance, Longevity and Weight Loss. I would like to see designs that use the color of green, gray, blue and white.

The final design should:

--convey a feeling of connectedness with positive transformation.

-- communicate the idea of awareness with guided effort that yields personal independence for a better and more productive life

Target Market(s)

Professionals who work in the IT/Computer/Engineering/Banking industry specifically Directors, Managers, CEO's.

Industry/Entity Type

Health And Wellness

Contact Information for Business Card

Dorvane Pike, Owner
email: DPIKE@verdelwellworks.example
tel: - 555-204-7718

Logo Text

better health through analytics or measure to manage

Font styles to use
Other font styles liked:
• Garamound

Colors
ffffff
abd037
85acd3
757575
34a7d7

Requirements
Must have
• Good contrast and decent size font - ease of readability, aesthetically nice colors
Nice to have
• image of chart or graph that conveys measurement or analytics
Should not have
• Borders, images of food,

```html
<!DOCTYPE html>
<html lang="en">
<head>
<meta charset="utf-8">
<title>Verdel Wellworks – Business Card</title>
<link rel="stylesheet" href="https://fonts.googleapis.com/css2?family=Oswald:wght@300&family=Open+Sans:wght@400;600;700&display=swap">
<style>
  :root {
    --backdrop: #ecebe8;
    --card-dark: #262626;
    --card-light: #ffffff;
    --green-light: #66b444;
    --green-dark: #0f6434;
    --ink: #2b2b2b;
    --ink-soft: #4a4a4a;
    --paper-edge: #d6d6d6;
  }
  * { box-sizing: border-box; margin: 0; padding: 0; }
  html, body { width: 1200px; height: 900px; overflow: hidden; }
  body { background: var(--backdrop); position: relative; font-family: "Open Sans", Arial, sans-serif; }

  .card {
    position: absolute;
    width: 630px;
    height: 360px;
    box-shadow: 0 3px 0 var(--paper-edge), 0 6px 0 #c8c8c8, 0 14px 24px rgba(0,0,0,.18);
    overflow: hidden;
  }

  /* Front */
  .card-front {
    left: 520px; top: 70px;
    background: repeating-linear-gradient(0deg, #2a2a2a 0 2px, #222 2px 4px);
    display: flex; flex-direction: column; align-items: center; justify-content: center;
    gap: 22px;
  }
  .front-mark {
    width: 46px; height: 46px; border-radius: 50%;
    border: 3px solid #fff;
  }
  .front-name {
    font-family: "Oswald", "Arial Narrow", sans-serif;
    font-weight: 300; font-size: 62px; letter-spacing: 1px; color: #fff;
  }

  /* Back */
  .card-back { left: 70px; top: 440px; background: var(--card-light); }
  .back-bands { position: absolute; inset: 0; }
  .holder { position: absolute; left: 34px; top: 30px; display: flex; align-items: flex-start; gap: 12px; }
  .holder-name { font-weight: 700; font-size: 21px; color: var(--green-light); line-height: 1.1; }
  .holder-name span { color: var(--green-dark); }
  .holder-role { font-size: 14px; color: var(--ink-soft); }

  .contact { position: absolute; left: 34px; top: 150px; font-size: 16px; color: var(--ink); line-height: 1.3; }
  .contact .address { margin-bottom: 14px; }
  .contact li { list-style: none; display: flex; align-items: center; gap: 8px; }
  .contact svg { width: 12px; height: 12px; fill: var(--green-dark); }

  .back-brand {
    position: absolute; right: 50px; top: 120px;
    display: flex; align-items: center; gap: 14px;
  }
  .back-brand-mark { width: 30px; height: 30px; border-radius: 50%; background: var(--green-light); }
  .back-brand-name { font-family: "Open Sans", Arial, sans-serif; font-weight: 600; font-size: 28px; color: var(--green-dark); }
</style>
</head>
<body>

<section class="card card-front" aria-label="Card front">
  <div class="front-mark"></div>
  <h1 class="front-name">Verdel Wellworks</h1>
</section>

<section class="card card-back" aria-label="Card back">
  <svg class="back-bands" viewBox="0 0 630 360" preserveAspectRatio="none">
    <polygon points="0,0 44,0 30,30 0,30" fill="var(--green-light)"/>
    <polygon points="0,245 300,330 300,360 0,360" fill="var(--green-light)"/>
    <polygon points="300,330 630,330 630,360 300,360" fill="var(--green-dark)"/>
    <polygon points="310,300 630,300 630,330 300,330" fill="var(--green-dark)"/>
  </svg>

  <div class="holder">
    <svg width="40" height="36" viewBox="0 0 40 36"><polygon points="0,36 28,0 40,0 40,36" fill="var(--green-dark)"/></svg>
    <div>
      <p class="holder-name">Dorvane <span>Pike</span></p>
      <p class="holder-role">Managing Director</p>
    </div>
  </div>

  <div class="contact">
    <p class="address">12345, Address Goes Here<br>Country Name, 123456</p>
    <ul>
      <li><svg viewBox="0 0 12 12"><path d="M2 1h3l1 3-2 1a7 7 0 0 0 3 3l1-2 3 1v3c-6 0-9-3-9-9z"/></svg>555-204-7718</li>
      <li><svg viewBox="0 0 12 12"><rect x="1" y="3" width="10" height="8" rx="1"/><rect x="3" y="0" width="6" height="3"/></svg>555-204-7719</li>
      <li><svg viewBox="0 0 12 12"><path d="M0 2h12v8H0z M0 2l6 5 6-5" /></svg>info@verdelwellworks.example</li>
    </ul>
  </div>

  <div class="back-brand">
    <div class="back-brand-mark"></div>
    <p class="back-brand-name">Verdel Wellworks</p>
  </div>
</section>

</body>
</html>
```